Voranta Imports Busisness cards and logo

Voranta imports is a brand new wholesale company located in Londonderry, New Hampshire dedicated to finding unique products from around the world.
Licensed to sell wine and spirits in the state and also authorized distributors of Pale Meadow Design, a manufacturer of girls and women shoes. Other products that we are currently trying to import are cheese and frozen food from Spain.
We would like a design that portraits our diversity of products and wholesale capabilities

```html
<!DOCTYPE html>
<html lang="en">
<head>
<meta charset="UTF-8">
<title>Voranta Imports – Business Card</title>
<link href="https://fonts.googleapis.com/css2?family=Play:wght@400;700&display=swap" rel="stylesheet">
<style>
  :root {
    --backdrop: #d9d6cf;
    --card: #ffffff;
    --card-shade: #eeeeee;
    --green-deep: #1f6b24;
    --green-mid: #2e8a30;
    --green-light: #8cc63f;
    --ink: #2b2b2b;
    --white: #ffffff;
  }
  html, body {
    margin: 0;
    padding: 0;
    width: 1200px;
    height: 899px;
    overflow: hidden;
    background: var(--backdrop);
    font-family: "Play", sans-serif;
  }
  .business-card {
    position: absolute;
    left: 100px;
    top: 164px;
    width: 1000px;
    height: 571px;
    background: radial-gradient(ellipse at 40% 45%, var(--card) 40%, var(--card-shade) 100%);
    box-shadow: 0 12px 30px rgba(0,0,0,0.25);
    overflow: hidden;
  }
  .accent-panel {
    position: absolute;
    inset: 0;
    width: 1000px;
    height: 571px;
  }
  .brand {
    position: absolute;
    left: 70px;
    top: 128px;
    display: flex;
    align-items: center;
    gap: 18px;
  }
  .brand-dot {
    width: 84px;
    height: 84px;
    border-radius: 50%;
    background: var(--green-light);
    flex: none;
  }
  .brand-name {
    font-weight: 700;
    font-size: 46px;
    color: var(--green-deep);
    letter-spacing: 0.3px;
    white-space: nowrap;
  }
  .address {
    position: absolute;
    left: 80px;
    top: 318px;
    font-size: 21px;
    line-height: 28px;
    color: var(--ink);
    letter-spacing: 1px;
  }
  .contact-list {
    position: absolute;
    left: 80px;
    top: 392px;
    margin: 0;
    padding: 0;
    list-style: none;
    font-size: 19px;
    color: var(--ink);
    letter-spacing: 1px;
  }
  .contact-list li {
    display: flex;
    align-items: center;
    gap: 14px;
    height: 30px;
  }
  .contact-icon {
    width: 20px;
    height: 20px;
    fill: var(--green-deep);
    flex: none;
  }
  .holder {
    position: absolute;
    right: 40px;
    top: 440px;
    text-align: right;
    color: var(--white);
    letter-spacing: 2px;
  }
  .holder-name {
    font-size: 30px;
    font-weight: 400;
  }
  .holder-role {
    font-size: 19px;
    margin-top: 2px;
  }
</style>
</head>
<body>
  <div class="business-card">
    <svg class="accent-panel" viewBox="0 0 1000 571" aria-hidden="true">
      <defs>
        <radialGradient id="panelGradient" cx="0.6" cy="0.3" r="0.8">
          <stop offset="0" stop-color="#3a9a3a"/>
          <stop offset="1" stop-color="#1c6320"/>
        </radialGradient>
      </defs>
      <path d="M690,0 C600,170 620,420 750,571 L1000,571 L1000,0 Z" fill="#8cc63f"/>
      <path d="M702,0 C614,170 634,420 762,571 L1000,571 L1000,0 Z" fill="url(#panelGradient)"/>
    </svg>

    <div class="brand">
      <div class="brand-dot"></div>
      <div class="brand-name">Voranta Imports</div>
    </div>

    <div class="address">214 Harbor Lane, Suite 9<br>Londonderry NH</div>

    <ul class="contact-list">
      <li>
        <svg class="contact-icon" viewBox="0 0 24 24"><path d="M6.6 10.8a15.1 15.1 0 0 0 6.6 6.6l2.2-2.2c.3-.3.7-.4 1-.2 1.1.4 2.3.6 3.6.6.6 0 1 .4 1 1V20c0 .6-.4 1-1 1C10.6 21 3 13.4 3 4c0-.6.4-1 1-1h3.5c.6 0 1 .4 1 1 0 1.3.2 2.5.6 3.6.1.3 0 .7-.2 1z"/></svg>
        <span>603 555 0147</span>
      </li>
      <li>
        <svg class="contact-icon" viewBox="0 0 24 24"><path d="M7 1h10a2 2 0 0 1 2 2v18a2 2 0 0 1-2 2H7a2 2 0 0 1-2-2V3a2 2 0 0 1 2-2zm0 3v14h10V4zm5 15.5a1.2 1.2 0 1 0 0 2.4 1.2 1.2 0 0 0 0-2.4z"/></svg>
        <span>603 555 0182</span>
      </li>
      <li>
        <svg class="contact-icon" viewBox="0 0 24 24"><path d="M7 2h9v5H7zM4 8h16a1 1 0 0 1 1 1v12H3V9a1 1 0 0 1 1-1zm3 4v2h2v-2zm4 0v2h2v-2zm4 0v2h2v-2zm-8 4v2h2v-2zm4 0v2h2v-2zm4 0v2h2v-2z"/></svg>
        <span>603 555 0199</span>
      </li>
      <li>
        <svg class="contact-icon" viewBox="0 0 24 24"><path d="M2 5h20v14H2zm2 2v.4l8 5.2 8-5.2V7zm0 2.8V17h16V9.8l-8 5.2z"/></svg>
        <span>hello@vorantaimports.com</span>
      </li>
      <li>
        <svg class="contact-icon" viewBox="0 0 24 24"><path d="M12 2a10 10 0 1 0 0 20 10 10 0 0 0 0-20zm6.9 9h-3a15 15 0 0 0-1.3-5.6A8 8 0 0 1 18.9 11zM12 4.1c.9 1.2 1.8 3.6 1.9 6.9h-3.8c.1-3.3 1-5.7 1.9-6.9zM9.4 5.4A15 15 0 0 0 8.1 11h-3a8 8 0 0 1 4.3-5.6zM5.1 13h3a15 15 0 0 0 1.3 5.6A8 8 0 0 1 5.1 13zm6.9 6.9c-.9-1.2-1.8-3.6-1.9-6.9h3.8c-.1 3.300-1 5.7-1.9 6.9zm2.6-1.3a15 15 0 0 0 1.3-5.6h3a8 8 0 0 1-4.3 5.6z"/></svg>
        <span>www.vorantaimports.com</span>
      </li>
    </ul>

    <div class="holder">
      <div class="holder-name">DANIEL PORTER</div>
      <div class="holder-role">FINANCIAL ADVISOR</div>
    </div>
  </div>
</body>
</html>
```